Business Intelligence Application - Reporting Menu and Report Criteria Design

Looking for a fresh, effective and user friendly view for the menu structure and reporting criteria screen format for a business reporting application. Initial format completed, content structure is in place, but we need the 'wow' design.. as its a serious professional report/BI tool it has to fall within certain guidelines for clarity and graphics..but we want it to be slick, friendly, great user experience. There is a large amount of complex content to fit into a small space and we need it to be very inviting, modern and intuitive.. If interested, please review the attachment. We have live screens in operation, but feel these could be improved and looking forward to seeing what great creative suggestions could be made. Please review work done to date in the attached.. We are not looking for a total re-design of everything, all the basic business content/structure is there.. but tell us what we could do to improve this in terms of graphic design... particularly the criteria screens.. thanks!
Updates

Reason: Need a few more days to review designs - thanks for all submissions so far, we will make a selection shortly.

Target Market(s)

Business analysts, hotel operations teams, finance analysts hospitality industry

Industry/Entity Type

Hospitality

Coding

Coded - Design and coding required

Number of Pages Required

4 page

Font styles to use
Sans Serif
Other font styles liked:
• Candara, please see example in deck

Colors
3276b5
3176b5
0255a3
85acd3
33a6d7
cee9f5
85cae6

Requirements
Must have
• sharp clear, logical menu structure, (currently it has 'clicks to sub-menus, we need hover over, slide to sub-menus..) colour, styling.. and most focus on revision of criteria.. right now is somewhat heavy, cumbersome.. keep colour and friendly intuitive process steps.. its heavy analytical stuff.. best of luck!
Should not have
• No grey fonts on white or grey screens! many business apps are not readable or sharp.. or fonts are too small.. colourless, so please avoid that.. see our deck - sharp dark (navy) or black fonts on white, or light shading..

```html
<!DOCTYPE html>
<html lang="en">
<head>
<meta charset="utf-8">
<title>Silver Crest Hotel &amp; Suites – Reporting Menu</title>
<link href="https://fonts.googleapis.com/css2?family=Cabin:wght@400;500;600;700&display=swap" rel="stylesheet">
<style>
  :root {
    --navy: #0255a3;
    --sky: #33a6d7;
    --sky-line: #85cae6;
    --ink: #111a24;
    --white: #ffffff;
    --border: #b9c3cc;
  }
  * { box-sizing: border-box; margin: 0; padding: 0; }
  html, body { width: 1200px; height: 422px; overflow: hidden; background: var(--white); }
  body { font-family: "Cabin", sans-serif; color: var(--ink); }
  .app { position: relative; width: 1200px; height: 422px; overflow: hidden; }

  .topbar { position: absolute; left: 0; top: 0; width: 1200px; height: 60px; background: var(--navy); color: var(--white); }
  .brand { position: absolute; left: 48px; top: 15px; display: flex; align-items: center; gap: 10px; }
  .brand-mark { width: 30px; height: 30px; border-radius: 50%; background: var(--white); }
  .brand-name { font-size: 18px; font-weight: 600; letter-spacing: -0.2px; }
  .welcome { position: absolute; left: 556px; top: 22px; font-size: 13px; }
  .today { position: absolute; left: 668px; top: 22px; font-size: 13px; }
  .top-btn { position: absolute; top: 11px; width: 107px; height: 37px; background: var(--sky); color: var(--white);
    font-size: 12px; font-weight: 600; display: flex; align-items: center; justify-content: center; letter-spacing: 0.3px; }
  .top-btn.intel { left: 834px; }
  .top-btn.planning { left: 956px; }
  .icon { position: absolute; top: 17px; width: 26px; height: 26px; }
  .icon.bell { left: 1084px; }
  .icon.share { left: 1126px; }

  .main-nav { position: absolute; left: 48px; top: 90px; display: flex; align-items: center; font-size: 12.8px; font-weight: 500; white-space: nowrap; }
  .main-nav .item { color: var(--ink); }
  .main-nav .item.active { color: var(--sky); }
  .main-nav .dot { width: 3px; height: 3px; border-radius: 50%; background: var(--sky); margin: 0 8px; }

  .search { position: absolute; left: 775px; top: 81px; width: 373px; height: 37px; border: 1px solid var(--border);
    display: flex; align-items: center; padding: 0 12px 0 17px; justify-content: space-between; font-size: 11.5px; color: var(--ink); }

  .caret { position: absolute; width: 0; height: 0; border-left: 10px solid transparent; border-right: 10px solid transparent; border-bottom: 11px solid var(--sky); }

  .sub-nav { position: absolute; left: 331px; top: 130px; width: 430px; height: 37px; background: var(--sky); color: var(--white);
    display: flex; align-items: center; padding-left: 15px; font-size: 12.5px; font-weight: 600; white-space: nowrap; }
  .sub-nav .dot { width: 3px; height: 3px; border-radius: 50%; background: var(--white); margin: 0 9px; }

  .menu { position: absolute; top: 190px; width: 163px; background: var(--sky); color: var(--white); box-shadow: 0 4px 12px rgba(2,85,163,0.15); }
  .menu.primary { left: 48px; }
  .menu.secondary { left: 224px; }
  .menu-row { height: 33.8px; padding: 0 11px; display: flex; align-items: center; justify-content: space-between; font-size: 10.5px; border-top: 1px solid var(--sky-line); }
  .menu-row:first-child { border-top: none; }
  .arrow { width: 0; height: 0; border-top: 4px solid transparent; border-bottom: 4px solid transparent; border-left: 5px solid var(--white); }
</style>
</head>
<body>
<div class="app">
  <header class="topbar">
    <div class="brand"><span class="brand-mark"></span><span class="brand-name">Silver Crest Hotel &amp; Suites</span></div>
    <span class="welcome">Welcome Admin</span>
    <span class="today">Tuesday October 04.2017</span>
    <span class="top-btn intel">INTEL</span>
    <span class="top-btn planning">PLANNING</span>
    <svg class="icon bell" viewBox="0 0 26 26" fill="none" stroke="#fff" stroke-width="1.4" stroke-linecap="round" stroke-linejoin="round" aria-label="Notifications">
      <path d="M8 17V11a5 5 0 0 1 10 0v6l1.5 2h-13z"/><path d="M11.5 21a1.6 1.6 0 0 0 3 0"/><path d="M13 4v2"/>
      <path d="M4.5 9a6 6 0 0 0 0 7"/><path d="M21.5 9a6 6 0 0 1 0 7"/>
    </svg>
    <svg class="icon share" viewBox="0 0 26 26" fill="none" stroke="#fff" stroke-width="1.4" stroke-linejoin="round" stroke-linecap="round" aria-label="Share">
      <path d="M15 4l8 6-8 6v-3.5c-5 0-8 1.5-10 5 0-6 4-10 10-10z"/><path d="M19 19v3H3V10h3"/>
    </svg>
  </header>

  <nav class="main-nav">
    <span class="item">Admin</span><span class="dot"></span>
    <span class="item active">Management</span><span class="dot"></span>
    <span class="item active">Rooms Performance</span><span class="dot"></span>
    <span class="item active">Revenue Summary</span><span class="dot"></span>
    <span class="item">Demand &amp; Risk</span><span class="dot"></span>
    <span class="item">Inventory Analysis</span><span class="dot"></span>
    <span class="item">Placeholder</span>
  </nav>

  <div class="search">
    <span>PROPERTY SEARCH</span>
    <svg width="14" height="14" viewBox="0 0 14 14" fill="none" stroke="#111a24" stroke-width="1.3"><circle cx="6" cy="6" r="4.6"/><path d="M9.4 9.4L13 13"/></svg>
  </div>

  <span class="caret" style="left:348px;top:119px"></span>
  <nav class="sub-nav">
    <span>Rollup Criteria</span><span class="dot"></span>
    <span>Report Criteria</span><span class="dot"></span>
    <span>Edit View</span><span class="dot"></span>
    <span>Saved View</span><span class="dot"></span>
    <span>Export</span>
  </nav>

  <span class="caret" style="left:59px;top:179px"></span>
  <ul class="menu primary">
    <li class="menu-row">Summaries<span class="arrow"></span></li>
    <li class="menu-row">Consolidations<span class="arrow"></span></li>
    <li class="menu-row">Communication<span class="arrow"></span></li>
    <li class="menu-row">Cheat Sheets<span class="arrow"></span></li>
    <li class="menu-row">Programs<span class="arrow"></span></li>
  </ul>

  <span class="caret" style="left:239px;top:179px"></span>
  <ul class="menu secondary">
    <li class="menu-row">Commpany Review</li>
    <li class="menu-row">Rooms Performance</li>
    <li class="menu-row">F&amp;B Performance</li>
    <li class="menu-row">Competitive Review</li>
    <li class="menu-row">Operations</li>
  </ul>
</div>
</body>
</html>
```